K7 Electrical Services Ltd Web design

I require a web site for my new electrical contracting company. We are customer service orientated. Offering high value electrical installations, design and maintenance. Focused on custom residential and commercial upgrading. Lighting design and application are paramount in our company's services. Industry leading product use and integration are always on the forefront with our customer client services. As well as energy efficiency.

Target Market(s)

Homebuilders, General Contractors, Property management companies, clients, individuals,

Industry/Entity Type

Electric Company

Coding

Coded - Design and coding required

Number of Pages Required

3 page

Requirements
Must have
• Classic, modern, edgy but not trendy . Appeals to the masse.
• 3 page
• home page
• about page
• gallery page
• ability to contact from the webiste
Nice to have
• open to all types of designs that are relative to the construction industry.
• Black, Grey, metallic ice blue and deep purple colours from the logo.
Should not have
• anything cheesy with cartoon light bulb images.

```html
<!DOCTYPE html>
<html lang="en">
<head>
<meta charset="utf-8">
<title>K7 Electrical Services Ltd</title>
<link rel="stylesheet" href="https://fonts.googleapis.com/css2?family=Montserrat:wght@400;500;600;700&family=Mulish:ital,wght@0,400;0,600;0,700;1,400&display=swap">
<style>
:root{
  --purple:#652c8f;
  --ink:#333333;
  --grey-text:#555555;
  --light-box:#ededed;
  --white:#ffffff;
  --footer-bar:#2b2b2b;
}
*{margin:0;padding:0;box-sizing:border-box}
html,body{width:1200px;height:2582px;overflow:hidden;background:var(--white)}
body{position:relative;font-family:"Mulish",Arial,sans-serif;color:var(--ink)}
.abs{position:absolute}

/* header */
.top-rule{left:0;top:0;width:1200px;height:4px;background:var(--purple)}
.brand{left:160px;top:58px;font:700 18px "Montserrat",sans-serif;color:var(--ink);white-space:nowrap;letter-spacing:0.3px}
.contact-mini{top:36px;font-size:13px;color:var(--grey-text);display:flex;align-items:center;gap:7px}
.login{left:952px;top:29px;width:86px;height:36px;border-radius:18px;background:var(--purple);color:var(--white);font:600 13px "Montserrat",sans-serif;display:flex;align-items:center;justify-content:center}
.main-nav{top:88px;left:0;width:1200px;font:600 12.5px "Montserrat",sans-serif;color:#222}
.main-nav span{position:absolute;white-space:nowrap}
.main-nav .active{color:var(--purple)}

/* hero */
.hero{left:0;top:129px;width:1200px;height:510px;background:linear-gradient(100deg,#2e4a6e 0%,#5d7698 35%,#c9a98a 65%,#f3c66e 85%,#f7dd97 100%)}
.hero-title{left:160px;top:318px;font:600 44px "Montserrat",sans-serif;color:var(--white);letter-spacing:0.5px}
.hero-btn{left:164px;top:393px;width:124px;height:41px;border:2px solid var(--white);border-radius:21px;color:var(--white);font:600 12.5px "Montserrat",sans-serif;display:flex;align-items:center;justify-content:center}
.hero-arrow{top:357px;width:33px;height:33px;border:1.5px solid rgba(255,255,255,.85);border-radius:50%;display:flex;align-items:center;justify-content:center}

/* section headings */
.section-title{left:0;width:1200px;text-align:center;font:600 29px "Montserrat",sans-serif;color:#444;display:flex;justify-content:center;align-items:center;gap:14px}
.section-title em{font-style:normal;color:var(--purple)}
.section-title .rule{display:inline-block;width:80px;height:2px;background:var(--purple)}
.lead{left:200px;width:800px;text-align:center;font-size:13.5px;line-height:22px;color:var(--grey-text)}

/* service boxes */
.service{top:799px;width:292px;height:267px;background:var(--light-box);text-align:center}
.service.featured{background:var(--purple);color:var(--white)}
.service svg{margin-top:30px}
.service h3{font:600 19px "Montserrat",sans-serif;color:#444;margin-top:14px}
.service.featured h3{color:var(--white)}
.service p{font-size:12px;line-height:22px;color:var(--grey-text);width:230px;margin:14px auto 0}
.service.featured p{color:#efe6f5}

/* testimonials */
.testimonials{left:0;top:1123px;width:1200px;height:323px;background:linear-gradient(120deg,#3e464d 0%,#5a636b 50%,#6f777d 100%)}
.notch{left:570px;top:1123px;width:0;height:0;border-left:30px solid transparent;border-right:30px solid transparent;border-top:28px solid var(--white)}
.testimonials-title{color:var(--white)}
.testimonials-title .rule{background:var(--white);width:60px;height:1.5px}
.quote{left:300px;top:1268px;width:600px;text-align:center;font-style:italic;font-size:12.5px;line-height:24px;color:#e8e8e8}
.quote-name{left:0;top:1362px;width:1200px;text-align:center;font-size:13.5px;color:#eeeeee}

/* what we do */
.work{top:1534px;width:275px}
.work .photo{width:275px;height:164px}
.work h3{font:600 17px "Montserrat",sans-serif;color:#333;margin-top:12px}
.work p{font-size:12.5px;line-height:22px;color:var(--grey-text);margin-top:8px}
.outline-btn{margin-top:14px;width:107px;height:35px;border:1.5px solid var(--purple);border-radius:18px;color:var(--purple);font-size:12.5px;display:flex;align-items:center;justify-content:center}

/* consultation */
.consult{left:0;top:1890px;width:1200px;height:376px;background:linear-gradient(120deg,#eceef1 0%,#f6f7f9 40%,#e8ebee 100%)}
.field{background:var(--white);border:1px solid #dcdcdc;font-size:12px;color:#444;padding:0 10px;display:flex;align-items:center}
.field.area{align-items:flex-start;padding-top:10px}
.submit{left:539px;top:2188px;width:122px;height:43px;border-radius:22px;background:var(--purple);color:var(--white);font:700 13px "Montserrat",sans-serif;display:flex;align-items:center;justify-content:center}

/* footer */
.footer{left:0;top:2266px;width:1200px;height:256px;background:var(--purple)}
.footer-brand{left:164px;top:2385px;font:700 14px "Montserrat",sans-serif;color:var(--white);white-space:nowrap}
.footer-col{top:2318px;color:var(--white)}
.footer-col h4{font:700 14.5px "Montserrat",sans-serif;margin-bottom:10px}
.footer-col li{list-style:none;font-size:12px;line-height:21px;color:#f0e8f6}
.footer-contact li{display:flex;gap:10px;margin-bottom:6px;align-items:flex-start;font-size:11.5px}
.footer-contact svg{flex:none;margin-top:1px}
.bottom-bar{left:0;top:2522px;width:1200px;height:60px;background:var(--footer-bar)}
.social{top:2538px;width:27px;height:27px;border:1.5px solid #bbbbbb;border-radius:50%}
.copyright{left:797px;top:2544px;font-size:11.5px;color:#cccccc}
</style>
</head>
<body>

<header>
  <div class="abs top-rule"></div>
  <div class="abs brand">K7 Electrical Services Ltd</div>
  <div class="abs contact-mini" style="left:642px">
    <svg width="11" height="11" viewBox="0 0 24 24"><path fill="#777" d="M6.6 10.8a15 15 0 006.6 6.6l2.2-2.2a1 1 0 011-.25 11 11 0 003.6.6 1 1 0 011 1V20a1 1 0 01-1 1A17 17 0 013 4a1 1 0 011-1h3.5a1 1 0 011 1c0 1.25.2 2.45.6 3.6a1 1 0 01-.25 1z"/></svg>
    800.555.0147
  </div>
  <div class="abs contact-mini" style="left:763px">
    <svg width="12" height="10" viewBox="0 0 24 18"><path fill="#777" d="M0 0h24v18H0z"/><path fill="#fff" d="M2 2l10 7 10-7"/></svg>
    hello@k7electrical.example
  </div>
  <div class="abs login">LOGIN</div>
  <nav class="abs main-nav">
    <span class="active" style="left:516px">HOME</span>
    <span style="left:597px">SERVICES</span>
    <span style="left:697px">WHAT WE DO</span>
    <span style="left:814px">BLOG</span>
    <span style="left:897px">ABOUT</span>
    <span style="left:976px">CONTACT</span>
  </nav>
</header>

<section>
  <div class="abs hero" role="img" aria-label="Electrical substation towers and power lines against a sunset sky"></div>
  <h1 class="abs hero-title">K7 ELECTRICAL</h1>
  <div class="abs hero-btn">READ MORE</div>
  <div class="abs hero-arrow" style="left:35px"><svg width="10" height="12" viewBox="0 0 10 12"><path d="M7 1L2 6l5 5" fill="none" stroke="#fff" stroke-width="1.5"/></svg></div>
  <div class="abs hero-arrow" style="left:1148px"><svg width="10" height="12" viewBox="0 0 10 12"><path d="M3 1l5 5-5 5" fill="none" stroke="#fff" stroke-width="1.5"/></svg></div>
</section>

<section>
  <h2 class="abs section-title" style="top:676px"><span class="rule"></span><span>WELCOME TO <em>K7 ELECTRICAL</em></span><span class="rule"></span></h2>
  <p class="abs lead" style="top:724px;left:240px;width:720px">Sed ut perspiciatis unde omnis iste natus error sit voluptatem accusantiuSed ut perspiciatis unde omnis iste natus error sit voluptatem accusanti doloremque laudantium, totam rem aperiam, eaque ipsa quae ab.m dolaudantium.</p>

  <div class="abs service" style="left:162px">
    <svg width="76" height="76" viewBox="0 0 76 76"><g fill="none" stroke="var(--purple)" stroke-width="7" stroke-linecap="round"><path d="M14 62L50 26"/><path d="M26 26L62 62"/></g><circle cx="56" cy="18" r="12" fill="var(--purple)"/><circle cx="60" cy="14" r="5" fill="var(--light-box)"/><rect x="12" y="10" width="16" height="8" fill="var(--purple)" transform="rotate(45 20 14)"/></svg>
    <h3>Electrical Installations</h3>
    <p>Sed ut perspiciatis unde omnis iste natus error sit voluptatem accusantiu m doloremque laudantium, tota.</p>
  </div>
  <div class="abs service featured" style="left:454px">
    <svg width="76" height="76" viewBox="0 0 76 76"><g fill="none" stroke="#fff" stroke-width="4" stroke-linejoin="round"><rect x="10" y="30" width="56" height="16" transform="rotate(-45 38 38)"/><path d="M20 12l44 44-4 10-10-4L6 18z"/></g></svg>
    <h3>Design</h3>
    <p>Sed ut perspiciatis unde omnis iste natus error sit voluptatem accusantiu m doloremque laudantium, tota.</p>
  </div>
  <div class="abs service" style="left:746px">
    <svg width="76" height="76" viewBox="0 0 76 76"><circle cx="34" cy="34" r="20" fill="none" stroke="var(--purple)" stroke-width="10" stroke-dasharray="8 5"/><circle cx="34" cy="34" r="15" fill="var(--purple)"/><circle cx="34" cy="34" r="7" fill="var(--light-box)"/><path d="M44 44l20 20" stroke="var(--purple)" stroke-width="8" stroke-linecap="round"/></svg>
    <h3>Maintenance</h3>
    <p>Sed ut perspiciatis unde omnis iste natus error sit voluptatem accusantiu m doloremque laudantium, tota.</p>
  </div>
</section>

<section>
  <div class="abs testimonials" role="img" aria-label="Transmission tower silhouettes against a grey sky"></div>
  <div class="abs notch"></div>
  <h2 class="abs section-title testimonials-title" style="top:1208px"><span class="rule"></span><span>CLIENT TESTIMONIALS</span><span class="rule"></span></h2>
  <svg class="abs" style="left:220px;top:1298px" width="40" height="14" viewBox="0 0 40 14"><path d="M39 7H2M8 1L2 7l6 6" fill="none" stroke="#fff" stroke-width="2"/></svg>
  <svg class="abs" style="left:940px;top:1298px" width="40" height="14" viewBox="0 0 40 14"><path d="M1 7h37M32 1l6 6-6 6" fill="none" stroke="#fff" stroke-width="2"/></svg>
  <p class="abs quote">Lorem ipsum dolor sit amet, consectetur adipiscing elit, sed do eiusmod tempor incididunt ut labore dolore magna aliqua. Ut enim ad minim veniam,Lorem ipsum dolor sit amet, consectetur adipiscing eiied do eiusmod tempor incididunt ut labore et dolore magna aliqua. Ut enim ad minim veniam,</p>
  <p class="abs quote-name">Dana Ray, Harbor Town</p>
</section>

<section>
  <h2 class="abs section-title" style="top:1467px"><span class="rule"></span><span>WHAT <em>WE DO</em></span><span class="rule"></span></h2>
  <article class="abs work" style="left:162px">
    <div class="photo" role="img" aria-label="Electrician in a hard hat working at a distribution panel" style="background:linear-gradient(120deg,#2f6fb3 0%,#8aa6bf 45%,#c7c9c6 100%)"></div>
    <h3>Custom Residential</h3>
    <p>Sed ut perspiciatis unde omnis iste Lorem loru m dolor sit amet, consectetur adipiscing elit ed do eiusmod tempor incididunted.</p>
    <div class="outline-btn">Read More</div>
  </article>
  <article class="abs work" style="left:463px">
    <div class="photo" role="img" aria-label="Power pylons at dusk" style="background:linear-gradient(180deg,#3b5575 0%,#7d7f8e 50%,#e09a52 85%,#b86a2e 100%)"></div>
    <h3>Commercial Upgrading</h3>
    <p>Sed ut perspiciatis unde omnis iste Lorem loru m dolor sit amet, consectetur adipiscing elit ed do eiusmod tempor incididunte.</p>
    <div class="outline-btn">Read More</div>
  </article>
  <article class="abs work" style="left:764px">
    <div class="photo" role="img" aria-label="House and garden lit with warm landscape lighting at night" style="background:linear-gradient(160deg,#1f2a22 0%,#3c4a35 40%,#b98d3a 75%,#e8c15a 100%)"></div>
    <h3>Lighting Designs</h3>
    <p>Sed ut perspiciatis unde omnis iste Lorem loru m dolor sit amet, consectetur adipiscing elit ed do eiusmod tempor incididunte.</p>
    <div class="outline-btn">Read More</div>
  </article>
</section>

<section>
  <div class="abs consult"></div>
  <h2 class="abs section-title" style="top:1940px"><span class="rule"></span><span>SCHEDULE A FREE <em>CONSULTATION</em></span><span class="rule"></span></h2>
  <p class="abs lead" style="top:1992px;left:230px;width:740px;font-size:14px;color:#444">Lorem ipsum dolor sit amet, consectetur adipiscing elit, sed do eiusmod tempor incididunt ut labore et dolore magna aliqua. Ut enim ad minim veniam, quis nostrud exercitation ullamco laboris nisi ut aliqui.</p>
  <div class="abs field" style="left:244px;top:2063px;width:348px;height:33px">Name:</div>
  <div class="abs field" style="left:244px;top:2102px;width:348px;height:33px">Phone:</div>
  <div class="abs field" style="left:244px;top:2143px;width:348px;height:33px">Email:</div>
  <div class="abs field area" style="left:604px;top:2063px;width:372px;height:113px">Comments:</div>
  <div class="abs submit">SUBMIT</div>
</section>

<footer>
  <div class="abs footer"></div>
  <div class="abs footer-brand">K7 Electrical Services Ltd</div>
  <div class="abs footer-col" style="left:396px">
    <h4>Works</h4>
    <ul><li>Lorem ipsum dolor</li><li>St amet, consectet</li><li>Ir adipiscing</li><li>Wellt, sed do eiu</li><li>Smod tempor</li><li>Gion ullamc.</li></ul>
  </div>
  <div class="abs footer-col" style="left:560px">
    <h4>Links</h4>
    <ul><li>Home</li><li>Residential</li><li>Commercial</li><li>Community</li><li>News</li><li>About</li></ul>
  </div>
  <div class="abs footer-col" style="left:684px">
    <h4>What We DO</h4>
    <ul><li>Residential Customers</li><li>Business Customers</li><li>Custom residential</li><li>Lighting design</li><li>Community</li><li>Careers</li></ul>
  </div>
  <div class="abs footer-col footer-contact" style="left:859px;width:240px">
    <h4>Contact</h4>
    <ul>
      <li><svg width="20" height="20" viewBox="0 0 20 20"><circle cx="10" cy="10" r="9" fill="none" stroke="#fff" stroke-width="1.3"/><path d="M10 15s-4-4-4-7a4 4 0 018 0c0 3-4 7-4 7z" fill="#fff"/><circle cx="10" cy="8" r="1.4" fill="var(--purple)"/></svg><span>Postal address: PO Box 00, Northvale Road 10, Northvale Ridge</span></li>
      <li><svg width="20" height="20" viewBox="0 0 20 20"><circle cx="10" cy="10" r="9" fill="none" stroke="#fff" stroke-width="1.3"/><path d="M7 6l2 2-1 1.5a6 6 0 002.5 2.5L12 11l2 2-1.5 1.5C9 14 6 11 5.5 7.5z" fill="#fff"/></svg><span>Phone: 908-555-0192</span></li>
      <li><svg width="20" height="20" viewBox="0 0 20 20"><circle cx="10" cy="10" r="9" fill="none" stroke="#fff" stroke-width="1.3"/><rect x="5.5" y="7" width="9" height="6.5" fill="#fff"/><path d="M5.5 7l4.5 3.5L14.5 7" fill="none" stroke="var(--purple)" stroke-width="1"/></svg><span>Email: office@k7electrical.example</span></li>
    </ul>
  </div>
  <div class="abs bottom-bar"></div>
  <div class="abs social" style="left:162px"></div>
  <div class="abs social" style="left:197px"></div>
  <div class="abs social" style="left:232px"></div>
  <div class="abs social" style="left:267px"></div>
  <p class="abs copyright">© 2018 K7 Electrical. All Rights are reserved.</p>
</footer>

</body>
</html>
```